Kestrel Facilities Business Card Design

We would now like to design business cards with the new Kestrel Facilities logo

Target Market(s)

Professional

Industry/Entity Type

Professional services

Contact Information for Business Card

Employee name, title, phone number, email address, corporate office address and logo.

Font styles to use
Sans Serif

Colors
0054AA
0677BA
7BADD7
CADEEF
E8F1F8

Requirements
Must have
• My logo
Should not have
• any other pictures or images besides my logo

```html
<!DOCTYPE html>
<html lang="en">
<head>
<meta charset="utf-8">
<title>Kestrel Facilities – Business Card</title>
<link rel="stylesheet" href="https://fonts.googleapis.com/css2?family=Oswald:wght@600&family=Montserrat:wght@400;500&display=swap">
<style>
  :root {
    --backdrop: #1c1c1c;
    --card: #232323;
    --card-pattern-a: #2b2b2b;
    --card-pattern-b: #353535;
    --brand-blue: #0677BA;
    --brand-blue-bright: #2f86cf;
    --text-light: #f2f2f2;
  }
  * { margin: 0; padding: 0; box-sizing: border-box; }
  html, body {
    width: 1200px; height: 900px; overflow: hidden;
    background: var(--backdrop);
  }
  .canvas { position: relative; width: 1200px; height: 900px; }
  .card {
    position: absolute; left: 320px; width: 560px; height: 320px;
    background: var(--card);
    box-shadow: 0 10px 30px rgba(0,0,0,0.55);
    overflow: hidden;
  }
  .card-back { top: 100px; }
  .card-front { top: 470px; }

  .back-texture {
    position: absolute; inset: 0;
    background: radial-gradient(ellipse at center, var(--card-pattern-b) 0%, var(--card-pattern-a) 100%);
  }
  .back-brand {
    position: absolute; left: 0; right: 0; top: 50%;
    transform: translateY(-50%);
    display: flex; align-items: center; justify-content: center; gap: 10px;
  }
  .back-brand .brand-square {
    width: 16px; height: 16px; background: var(--brand-blue-bright);
  }
  .back-brand .brand-name {
    font-family: "Oswald", sans-serif; font-weight: 600;
    font-size: 26px; letter-spacing: 1px; text-transform: uppercase;
    color: var(--brand-blue-bright);
  }

  .front-layout {
    position: absolute; inset: 0;
    display: flex; align-items: center; justify-content: center;
    padding: 0 40px;
  }
  .identity { text-align: right; padding-right: 20px; white-space: nowrap; }
  .person-name {
    font-family: "Oswald", sans-serif; font-weight: 600;
    font-size: 30px; line-height: 1; letter-spacing: 0.3px;
    color: var(--brand-blue-bright); text-transform: uppercase;
    white-space: nowrap;
  }
  .person-title {
    font-family: "Montserrat", sans-serif; font-weight: 500;
    font-size: 13px; color: var(--text-light); margin-top: 6px;
  }
  .divider { width: 2px; height: 88px; background: var(--brand-blue); flex: none; }
  .contact {
    padding-left: 20px;
    font-family: "Montserrat", sans-serif; font-weight: 400;
    font-size: 12px; line-height: 1.5; color: var(--text-light);
    list-style: none; white-space: nowrap;
  }
  .contact li { display: flex; align-items: center; gap: 7px; }
  .contact .icon { width: 12px; height: 12px; flex: none; }
  .contact .address { display: block; }
</style>
</head>
<body>
<div class="canvas">

  <section class="card card-back" aria-label="Business card back">
    <div class="back-texture" role="img" aria-label="Tone-on-tone repeating brand pattern"></div>
    <div class="back-brand">
      <span class="brand-square"></span>
      <span class="brand-name">Kestrel Facilities</span>
    </div>
  </section>

  <section class="card card-front" aria-label="Business card front">
    <div class="front-layout">
      <div class="identity">
        <h1 class="person-name">Daniel Whitford</h1>
        <p class="person-title">Director</p>
      </div>
      <div class="divider"></div>
      <ul class="contact">
        <li class="address">1187 Larch Creek Road<br>Corvallis, OR 97330</li>
        <li>
          <svg class="icon" viewBox="0 0 24 24" aria-hidden="true">
            <path d="M6.6 10.8a15 15 0 0 0 6.6 6.6l2.2-2.2a1 1 0 0 1 1-.25 11.4 11.4 0 0 0 3.6.57 1 1 0 0 1 1 1V20a1 1 0 0 1-1 1A17 17 0 0 1 3 4a1 1 0 0 1 1-1h3.5a1 1 0 0 1 1 1c0 1.25.2 2.45.57 3.6a1 1 0 0 1-.25 1z" fill="var(--brand-blue-bright)"/>
          </svg>
          (541) 555-0142
        </li>
        <li>
          <svg class="icon" viewBox="0 0 24 24" aria-hidden="true">
            <rect x="2.5" y="5" width="19" height="14" fill="none" stroke="var(--brand-blue-bright)" stroke-width="2"/>
            <path d="M3 6l9 7 9-7" fill="none" stroke="var(--brand-blue-bright)" stroke-width="2"/>
          </svg>
          info@kestrelfacilities.com
        </li>
      </ul>
    </div>
  </section>

</div>
</body>
</html>
```